Automotive Accessories Business Card

Design a business template that match our new logo design and our industry.

https://www.qelmotorgear.com/

Target Market(s)

Aftermarket auto parts and accessories

Industry/Entity Type

automotive

Contact Information for Business Card

company logo

Font styles to use
Serif
Sans Serif

Colors
EB3D1F
EC4F4E
F09395
F8D3D4
FCEDEE

```html
<!DOCTYPE html>
<html lang="en">
<head>
<meta charset="utf-8">
<title>QEL Motor Gear – Business Card</title>
<link href="https://fonts.googleapis.com/css2?family=Montserrat:wght@400;500;800&display=swap" rel="stylesheet">
<style>
  :root {
    --backdrop: #2b2b2d;
    --card: #464648;
    --card-mark: #3b3b3d;
    --red: #e21f26;
    --white: #ffffff;
    --text: #f2f2f2;
  }
  * { box-sizing: border-box; margin: 0; padding: 0; }
  html, body {
    width: 1200px; height: 900px; overflow: hidden;
    background: var(--backdrop);
    font-family: "Montserrat", sans-serif;
  }
  .sheet {
    width: 1200px; height: 900px;
    display: flex; flex-direction: column; align-items: center; justify-content: center;
    gap: 36px;
  }
  .card {
    position: relative;
    width: 720px; height: 411px;
    background: var(--card);
    border-bottom: 8px solid var(--red);
    box-shadow: 0 12px 30px rgba(0,0,0,.45);
  }
  /* front */
  .card--front { display: flex; align-items: center; justify-content: center; }
  .brand-mark--faint {
    display: flex; align-items: center; gap: 18px;
    color: var(--card-mark);
    font-weight: 800; font-size: 54px; letter-spacing: 2px;
  }
  .brand-mark--faint .brand-square { background: var(--card-mark); }
  .brand-square { width: 34px; height: 34px; display: block; }

  /* back */
  .card--back { display: flex; align-items: center; }
  .brand-block {
    width: 360px; display: flex; align-items: center; justify-content: center; gap: 14px;
  }
  .brand-block .brand-square { background: var(--red); width: 26px; height: 26px; }
  .brand-name {
    color: var(--white); font-weight: 800; font-size: 30px; letter-spacing: 1px;
    line-height: 1.1;
  }
  .divider { width: 1px; height: 210px; background: var(--red); }
  .contact { padding-left: 34px; color: var(--text); font-size: 15px; line-height: 1.35; }
  .contact__name {
    color: var(--red); font-weight: 800; font-size: 26px; letter-spacing: 1px;
  }
  .contact__role { font-size: 16px; margin-bottom: 16px; }
  .contact__address { margin-bottom: 16px; }
  .contact__list { list-style: none; }
  .contact__list li { display: flex; align-items: center; gap: 9px; }
  .contact__list svg { width: 12px; height: 12px; fill: var(--red); flex: none; }
</style>
</head>
<body>
<main class="sheet">
  <section class="card card--front" aria-label="Card front">
    <div class="brand-mark--faint">
      <span class="brand-square"></span>
      <span>QEL MOTOR GEAR</span>
    </div>
  </section>

  <section class="card card--back" aria-label="Card back">
    <div class="brand-block">
      <span class="brand-square"></span>
      <span class="brand-name">QEL MOTOR GEAR</span>
    </div>
    <div class="divider"></div>
    <div class="contact">
      <p class="contact__name">DORIAN VALE</p>
      <p class="contact__role">CEO/Founder</p>
      <p class="contact__address">482 Larkspur Ave. Unit C<br>Fenwick, CA, 90412</p>
      <ul class="contact__list">
        <li>
          <svg viewBox="0 0 12 12" aria-hidden="true"><path d="M2.5 0.5l2 2.2-1.1 1.4c.7 1.5 1.9 2.7 3.4 3.4l1.4-1.1 2.3 2-1.2 2.1C4.9 10.3 1.6 7 1.1 2.7z"/></svg>
          <span>1-800-555-0148</span>
        </li>
        <li>
          <svg viewBox="0 0 12 12" aria-hidden="true"><path d="M0 2h12v8H0z M0 2l6 4 6-4" stroke="#464648" stroke-width="1"/></svg>
          <span>sales@qelmotorgear.com</span>
        </li>
        <li>
          <svg viewBox="0 0 12 12" aria-hidden="true"><circle cx="6" cy="6" r="5.5"/><path d="M0.5 6h11M6 0.5v11" stroke="#464648" stroke-width="1"/></svg>
          <span>www.qelmotorgear.com</span>
        </li>
      </ul>
    </div>
  </section>
</main>
</body>
</html>
```